Personal Trainer website design

We are working with a personal trainer to design a website. They offer their primary services: Diet Coaching, In-Person Coaching (workouts), and Remote Coaching.
Some sites we like: https://www.mirabelthorne.com, https://kavialune.com/en-us, https://corvexfit.co.uk
Thank you for taking the time to consider designing a website for us. We are web developers based in Stockton, CA USA. Most of our projects go through the same process. Understanding this process may help you win a project with us. We custom-code all of our websites in-house. We don’t have any requirements as to what tools you use for your design, but ask that you follow these guidelines.
IMAGES:
We ask that if you use any images, or icons in the design, have a link to the asset, so we can purchase the image/icon. Most of the designs we submit do not have the customer’s images on them unless they have some great images. Be creative; show us the feeling that you are trying to portray with your image choices. Use any royalty-free site you choose. We subscribe to Quillon and mostly use their images, but are ok to purchase images outside of Quillon.
FONTS:
We ask that you identify the fonts you’re using in the design. This can be done in a message if you want. We typically use Brivane Fonts and Quillon Fonts.
CONTENT:
We're always open to different content and ideas. Often, we submit designs with stock images so that the client can see our vision. We typically go back and take pictures after the website launch to use their images with our vision. Lorem Ipsum is fine for paragraphs, but we ask that you make the Headers with correct English. We want to be able to show the vision and identify the sections of the website.
INSPIRATION:
We try and add a couple of links in the brief of some websites that we like to help you get started in your design.
REVISIONS:
We do not often ask for revisions of the designs unless we see something in the design that may not appeal to the client. If there are slight changes that we want to make, we simply do that in the development process.
FEEDBACK:
We rarely give feedback on designs during the design process. We are working on many website projects and do not have the time to give feedback. We usually respond if your request is well thought out and asks specific questions, but a note asking “feedback, please” usually goes unanswered.
1 page

```html
<!DOCTYPE html>
<html lang="en">
<head>
<meta charset="utf-8">
<title>Nivafit — Personal Trainer</title>
<link rel="stylesheet" href="https://fonts.googleapis.com/css2?family=DM+Serif+Display&family=Poppins:wght@400;500;600&family=Oswald:wght@500&display=swap">
<style>
:root{
  --olive:#8a9a1b;
  --olive-soft:#b7c06a;
  --ink:#1f1f1f;
  --muted:#555;
  --stage:#e8ebd6;
  --paper:#ffffff;
  --sand:#e2dfd9;
  --footer:#d9d6d0;
  --wine:#7c1a26;
  --maroon:#5b0f16;
  --taupe:#6a5a47;
}
*{box-sizing:border-box;margin:0;padding:0}
html,body{width:1200px;height:1200px;overflow:hidden;background:var(--stage);font-family:"Poppins",sans-serif;color:var(--ink)}
.page{position:absolute;left:355px;top:0;width:490px;height:1200px;background:var(--paper);overflow:hidden}
.abs{position:absolute}
.serif{font-family:"DM Serif Display",serif;font-weight:400}
.accent{color:var(--olive)}
.eyebrow{font-size:5px;color:var(--ink)}
.body-text{font-size:3.6px;line-height:1.55;color:var(--ink)}
.btn{position:absolute;height:12px;border-radius:6px;background:var(--olive);color:#fff;font-size:3.6px;display:flex;align-items:center;justify-content:center;letter-spacing:.1px}
.btn.ghost{background:var(--sand);color:var(--ink)}
.photo{position:absolute}
.brand{display:flex;align-items:center;gap:4px;font-weight:600;color:var(--ink)}
.brand .dot{width:14px;height:14px;border-radius:50%;background:var(--olive)}
/* hero */
.nav{left:65px;top:60px;display:flex;gap:6px;align-items:center;font-size:3.6px}
.nav .members{background:var(--olive);color:#fff;padding:4px 7px;border-radius:6px}
.hero-title{left:65px;top:96px;font-size:16px;line-height:1.02}
.search{left:411px;top:10px;width:12px;height:12px;border-radius:50%;background:var(--olive)}
/* about */
.frame{border:1.3px solid var(--olive);border-radius:5px}
.stats{left:248px;top:342px;width:242px;height:48px;background:var(--olive);display:flex;color:#fff}
.stat{width:61px;text-align:center;padding-top:9px}
.stat .num{font-size:12px;line-height:1}
.stat .num sup{font-size:6px}
.stat .lbl{font-size:4.6px;line-height:1.4;margin-top:2px}
.stats .gap{position:absolute;left:181px;top:0;width:2px;height:48px;background:#fff}
/* why */
.ticks{left:65px;top:492px;list-style:none;font-size:3.6px}
.ticks li{display:flex;align-items:center;gap:3px;height:8.6px}
/* services */
.service-list{left:248px;top:657px;font-size:25px;line-height:30.6px;color:var(--taupe)}
.service-list .first{color:var(--maroon)}
.cards{left:65px;top:843px;display:flex;gap:7.7px}
.card{width:53.5px;height:53px;background:var(--sand);border-radius:3px;display:flex;flex-direction:column;align-items:center;padding-top:8px}
.card p{font-size:3.2px;text-align:center;line-height:1.4;margin-top:6px;width:42px}
/* press */
.check{left:64px;top:924px;font-family:"Oswald",sans-serif;font-size:8px;line-height:1.3}
.press{left:125px;top:920px;width:268px;height:46px;background:var(--sand);border-radius:3px;display:flex;justify-content:space-around;align-items:center;font-size:15px;color:#555}
/* testimonials */
.t-card{position:absolute;top:989px;height:74px;background:#f2f1ee;border-radius:3px}
.t-card.faded{opacity:.45}
.avatar{position:absolute;width:48px;height:48px;border-radius:50%;border:1px solid #ccc}
.t-name{font-size:5.6px;color:var(--olive)}
.t-role{font-size:3.2px;color:var(--muted)}
.stars{font-size:4px;color:var(--olive);letter-spacing:.5px}
/* footer */
.footer{left:0;top:1093px;width:490px;height:107px;background:var(--footer)}
.f-head{font-size:6.2px;font-weight:500}
.f-links{font-size:3.8px;line-height:7.6px}
.socials{display:flex;gap:4px}
.socials span{width:8px;height:8px;border-radius:50%;background:var(--ink)}
.pays{display:flex;gap:3px}
.pays span{width:11px;height:6px;border-radius:1px;background:#fff;border:.5px solid #bbb}
</style>
</head>
<body>
<main class="page">

  <!-- hero -->
  <div class="abs brand" style="left:65px;top:24px;font-size:15px"><span class="dot"></span>NIVAFIT</div>
  <nav class="abs nav">
    <span>ABOUT</span><span>SERVICES</span><span>THE JOURNAL</span><span>BLOG</span><span>SHOP</span><span>CONTACT</span><span class="members">MEMBERS</span>
  </nav>
  <p class="abs eyebrow" style="left:66px;top:84px">Your personal workout and diet trainer</p>
  <h1 class="abs serif hero-title">A <span class="accent">healthy</span> outside starts<br><span class="accent">from</span> the <span class="accent">inside</span>.</h1>
  <p class="abs" style="left:65px;top:134px;font-size:4.6px">- Dalen Moray</p>
  <p class="abs body-text" style="left:65px;top:147px;width:150px">Lorem ipsum dolor sit amet, consectetur adipiscing elit. Vestibulum vel fringilla mi. Integer eu sagittis quam, sit amet volutpat odio. Sed et tincidunt nisi. Integer eget felis quis nulla tincidunt commodo. Sed at tincidunt eros.</p>
  <div class="btn" style="left:65px;top:177px;width:40px">GET STARTED</div>
  <div class="photo" role="img" aria-label="Trainer guiding a smiling woman on a gym machine in a bright white studio" style="left:245px;top:0;width:245px;height:205px;background:linear-gradient(135deg,#f1f0ec,#d9d6cf 60%,#bdb7ad);border-bottom-left-radius:4px"></div>
  <div class="abs search"></div>

  <!-- about -->
  <div class="abs frame" style="left:65px;top:234px;width:176px;height:160px"></div>
  <div class="photo" role="img" aria-label="Trainer and client reviewing a workout plan on a clipboard in a gym" style="left:73px;top:243px;width:160px;height:143px;border-radius:3px;background:linear-gradient(120deg,#8b8883,#5c5a57 55%,#a39f98)"></div>
  <p class="abs eyebrow" style="left:248px;top:237px">Our Mission, Vission, Passion and History</p>
  <h2 class="abs serif" style="left:248px;top:250px;font-size:10.5px">About <span class="accent">Nivafit</span></h2>
  <p class="abs body-text" style="left:248px;top:266px;width:175px">Curabitur tincidunt velit quam, eu condimentum ligula bibendum ac. Duis volutpat mauris eu lacinia lobortis. Nulla facilisi. In accumsan sed massa sit amet pellentesque. Mauris tristique, nunc pharetra vestibulum tempus, ex sem molestie neque, ac varius risus lacus sit amet purus. Cras <span class="accent">laoreet</span> dignissim felis, ac congue augue. Donec blandit sem quis tortor hendrerit mattis. Mauris vitae ultricies libero. Curabitur suscipit dignissim augue, eleifend iaculis quam pellentesque eu. Suspendisse et eros fermentum, rhoncus nulla eu, pharetra sem. Sed pulvinar luctus sodales.</p>
  <div class="btn" style="left:248px;top:319px;width:40px">GET STARTED</div>
  <div class="abs stats">
    <div class="stat"><div class="num serif">100<sup>+</sup></div><div class="lbl">On Demand<br>Classes</div></div>
    <div class="stat"><div class="num serif">30<sup>+</sup></div><div class="lbl">Live Stream<br>Classes</div></div>
    <div class="stat"><div class="num serif">50<sup>+</sup></div><div class="lbl">Private workout<br>classes</div></div>
    <div class="gap"></div>
  </div>

  <!-- why choose -->
  <p class="abs eyebrow" style="left:65px;top:444px">Our Facilities, Uniqueness And Features</p>
  <h2 class="abs serif" style="left:65px;top:458px;font-size:10.5px">Why choose <span class="accent">Nivafit</span></h2>
  <p class="abs body-text" style="left:65px;top:474px;width:140px">Curabitur tincidunt velit quam, eu condimentum ligula bibendum ac. Duis volutpat mauris eu lacinia lobortis.</p>
  <ul class="abs ticks">
    <li><svg width="5" height="5" viewBox="0 0 10 10"><path d="M1 5l3 3 5-7" fill="none" stroke="#8a9a1b" stroke-width="2"/></svg>Lorem ipsum dolor sit amet</li>
    <li><svg width="5" height="5" viewBox="0 0 10 10"><path d="M1 5l3 3 5-7" fill="none" stroke="#8a9a1b" stroke-width="2"/></svg>Consectetur adipiscing elit</li>
    <li><svg width="5" height="5" viewBox="0 0 10 10"><path d="M1 5l3 3 5-7" fill="none" stroke="#8a9a1b" stroke-width="2"/></svg>Sed do eiusmod tempor incididunt</li>
    <li><svg width="5" height="5" viewBox="0 0 10 10"><path d="M1 5l3 3 5-7" fill="none" stroke="#8a9a1b" stroke-width="2"/></svg>Ut labore et dolore magna aliqua.</li>
    <li><svg width="5" height="5" viewBox="0 0 10 10"><path d="M1 5l3 3 5-7" fill="none" stroke="#8a9a1b" stroke-width="2"/></svg>Quis ipsum suspendisse ultrices gravida.</li>
  </ul>
  <div class="btn" style="left:65px;top:542px;width:40px">GET STARTED</div>
  <div class="btn ghost" style="left:109px;top:542px;width:39px">BOOK NOW</div>
  <svg class="abs" style="left:263px;top:429px" width="32" height="20"><path d="M1 20V5a4 4 0 0 1 4-4h27" fill="none" stroke="#8a9a1b" stroke-width="1.2"/></svg>
  <div class="photo" role="img" aria-label="Instructor helping a woman stretch on a yoga mat in a light studio" style="left:293px;top:420px;width:131px;height:159px;border-radius:3px;background:linear-gradient(160deg,#e6e5e2,#b9b6b1 60%,#55524e)"></div>
  <div class="photo" role="img" aria-label="Trainer writing on a clipboard beside a smiling client" style="left:248px;top:452px;width:84px;height:111px;border:2px solid #fff;background:linear-gradient(150deg,#d5d3cf,#8d8a85 60%,#3e3c3a)"></div>

  <!-- services -->
  <p class="abs eyebrow" style="left:65px;top:604px">Make A New Start With The New You</p>
  <h2 class="abs serif" style="left:65px;top:618px;font-size:10.5px">Services from <span class="accent">Nivafit</span></h2>
  <p class="abs body-text" style="left:65px;top:635px;width:175px">Curabitur tincidunt velit quam, eu condimentum ligula bibendum ac. Duis volutpat mauris eu lacinia lobortis. Nulla facilisi. In accumsan sed massa sit amet pellentesque.</p>
  <div class="photo" role="img" aria-label="Athlete in a deep forward stretch on a red studio floor" style="left:65px;top:658px;width:174px;height:174px;border-radius:3px;background:radial-gradient(circle at 55% 40%,#9b2a38,#6e1520 70%,#5a0f18)"></div>
  <h3 class="abs serif" style="left:73px;top:722px;font-size:21px;color:#fff">Studio Classes</h3>
  <div class="abs" style="left:74px;top:748px;width:14px;height:.7px;background:#fff"></div>
  <p class="abs body-text" style="left:74px;top:753px;width:152px;color:#fff">Curabitur tincidunt velit quam, eu condimentum ligula bibendum ac. Duis volutpat mauris eu lacinia lobortis. Nulla facilisi. In accumsan sed massa.</p>
  <div class="abs" style="left:74px;top:768px;width:38px;height:7px;border-radius:4px;background:#fff;font-size:3.4px;display:flex;align-items:center;justify-content:center">Know More &rarr;</div>
  <div class="abs serif service-list">
    <div class="first">Studio classes</div><div>Personal</div><div>Training</div><div>Live Classes</div><div>Diet Coaching</div><div>In-Person</div>
  </div>
  <div class="abs cards">
    <div class="card"><svg width="18" height="18" viewBox="0 0 24 24" fill="none" stroke="#333" stroke-width="1"><rect x="3" y="4" width="18" height="12"/><path d="M8 20h8M12 16v4"/></svg><p>Lorem ipsum dolor sit amet, consectetur adipiscing elit.</p></div>
    <div class="card"><svg width="18" height="18" viewBox="0 0 24 24" fill="none" stroke="#333" stroke-width="1"><rect x="8" y="3" width="13" height="16"/><path d="M11 7h7M11 10h7M11 13h5"/><circle cx="5" cy="15" r="2"/></svg><p>Lorem ipsum dolor sit amet, consectetur adipiscing elit.</p></div>
    <div class="card"><svg width="18" height="18" viewBox="0 0 24 24" fill="none" stroke="#333" stroke-width="1"><rect x="3" y="4" width="18" height="13"/><circle cx="12" cy="10" r="2.5"/><path d="M6 21h12"/></svg><p>Lorem ipsum dolor sit amet, consectetur adipiscing elit.</p></div>
    <div class="card"><svg width="18" height="18" viewBox="0 0 24 24" fill="none" stroke="#333" stroke-width="1"><rect x="5" y="4" width="12" height="17"/><path d="M8 9h6M8 12h6M8 15h3"/><circle cx="18" cy="17" r="3"/></svg><p>Lorem ipsum dolor sit amet, consectetur adipiscing elit.</p></div>
    <div class="card"><svg width="18" height="18" viewBox="0 0 24 24" fill="none" stroke="#333" stroke-width="1"><path d="M3 6h18M5 4v4M19 4v4"/><circle cx="12" cy="9" r="2"/><path d="M12 11v6M9 21l3-4 3 4"/></svg><p>Lorem ipsum dolor sit amet, consectetur adipiscing elit.</p></div>
    <div class="card"><svg width="18" height="18" viewBox="0 0 24 24" fill="none" stroke="#333" stroke-width="1"><rect x="3" y="4" width="18" height="15"/><circle cx="9" cy="10" r="2"/><path d="M6 16c1-2 5-2 6 0M14 9h4M14 12h4"/></svg><p>Lorem ipsum dolor sit amet, consectetur adipiscing elit.</p></div>
  </div>

  <!-- press -->
  <div class="abs check"><span class="accent">CHECK</span><br>US ON</div>
  <svg class="abs" style="left:103px;top:938px" width="16" height="8"><path d="M15 4H2M6 1L2 4l4 3" fill="none" stroke="#222" stroke-width="1.4"/></svg>
  <div class="abs press serif"><span>VELLUNE</span><span>Harlow</span><span style="font-size:11px">The Meridian</span><span>CORSAIRE</span></div>
  <svg class="abs" style="left:400px;top:938px" width="16" height="8"><path d="M1 4h13M10 1l4 3-4 3" fill="none" stroke="#222" stroke-width="1.4"/></svg>

  <!-- testimonials -->
  <div class="t-card faded" style="left:0;width:119px">
    <div class="abs" style="left:4px;top:10px"><div class="t-name">Evan Calder</div><div class="t-role">CEO, ABC Industries</div><div class="stars">★★★★★</div></div>
    <p class="abs body-text" style="left:4px;top:38px;width:110px">Lorem ipsum dolor sit amet, consectetur adipiscing elit, sed do eiusmod tempor incididunt ut labore et dolore magna aliqua.</p>
  </div>
  <svg class="abs" style="left:135px;top:1023px" width="14" height="6"><path d="M13 3H2M5 .5L2 3l3 2.5" fill="none" stroke="#8a9a1b" stroke-width="1.2"/></svg>
  <div class="t-card" style="left:157px;width:176px">
    <div class="avatar" role="img" aria-label="Portrait of client" style="left:5px;top:13px;background:linear-gradient(#e9e7e3,#c9c5bf)"></div>
    <div class="abs" style="left:62px;top:12px"><div class="t-name">John Doe</div><div class="t-role">Marketing Manager, ABCD</div><div class="stars">★★★★★</div></div>
    <p class="abs body-text" style="left:62px;top:39px;width:108px">Lorem ipsum dolor sit amet, consectetur adipiscing elit, sed do eiusmod tempor incididunt ut labore et dolore magna aliqua. Quis ipsum suspendisse ultrices gravida. Risus commodo viverra maecenas accumsan lacus vel fac.</p>
  </div>
  <svg class="abs" style="left:339px;top:1023px" width="14" height="6"><path d="M1 3h11M9 .5L12 3 9 5.5" fill="none" stroke="#8a9a1b" stroke-width="1.2"/></svg>
  <div class="t-card faded" style="left:371px;width:119px">
    <div class="avatar" role="img" aria-label="Portrait of client" style="left:5px;top:13px;background:linear-gradient(#8d8782,#4e4845)"></div>
    <div class="abs" style="left:62px;top:12px"><div class="t-name">Lena Ostrow</div><div class="t-role">Actor, Ex Model</div><div class="stars">★★★★★</div></div>
    <p class="abs body-text" style="left:62px;top:39px;width:56px">Lorem ipsum dolor sit amet, do eiusmod tempor incididunt.</p>
  </div>

  <!-- footer -->
  <footer class="abs footer">
    <div class="abs brand" style="left:65px;top:28px;font-size:12px"><span class="dot" style="width:11px;height:11px"></span>NIVAFIT</div>
    <div class="abs socials" style="left:65px;top:57px"><span></span><span></span><span></span><span></span><span></span></div>
    <div class="abs pays" style="left:65px;top:71px"><span></span><span></span><span></span><span></span><span></span><span></span></div>
    <div class="abs" style="left:188px;top:31px"><div class="f-head">QUICK LINKS</div>
      <div style="display:flex;gap:12px;margin-top:2px"><div class="f-links">About<br>Services<br>The Journal<br>Blog<br>Shop</div><div class="f-links">Contact<br>Faq<br>Member<br>Signup<br>Sitemap</div></div></div>
    <div class="abs" style="left:280px;top:31px"><div class="f-head">CONNECT WITH US</div>
      <div class="f-links" style="margin-top:2px">info@nivafit.com<br>support@nivafit.com</div>
      <div class="f-links" style="margin-top:3px">&#9742; 0123 555 0198<br>&#9742; 0123 555 0142<br>&#9873; ABCD, Lorem ipsum, State, Fine – 12345</div></div>
    <div class="abs" style="left:372px;top:31px"><div class="f-head">OTHER LINKS</div>
      <div class="f-links" style="margin-top:2px">Search<br>Privacy Policy<br>Terms of Service<br>Members</div></div>
    <p class="abs" style="left:343px;top:91px;font-size:3.6px">Copyright © 2023, <span class="accent">Nivafit</span> All rights reserved.</p>
  </footer>
</main>
</body>
</html>
```